wealth management firm, professional group, new model

we have a logo that works but we need a card, white background using our colors...clean look

our tag line if can be used in

The Bridge From Client to Owner

```html
<!DOCTYPE html>
<html lang="en">
<head>
<meta charset="utf-8">
<title>Jordan Hale — Business Card</title>
<link rel="stylesheet" href="https://fonts.googleapis.com/css2?family=Montserrat:wght@500;600;700&display=swap">
<style>
  :root {
    --card-white: #ffffff;
    --ink-navy: #1b2947;
    --canvas-size-w: 1200px;
    --canvas-size-h: 896px;
  }
  * { margin: 0; padding: 0; box-sizing: border-box; }
  html, body {
    width: var(--canvas-size-w);
    height: var(--canvas-size-h);
    overflow: hidden;
    background: var(--card-white);
  }
  .business-card {
    position: relative;
    width: var(--canvas-size-w);
    height: var(--canvas-size-h);
    background: var(--card-white);
    color: var(--ink-navy);
    font-family: "Montserrat", Arial, sans-serif;
    text-align: center;
  }
  .identity {
    position: absolute;
    top: 190px;
    left: 0;
    right: 0;
  }
  .person-name {
    font-weight: 700;
    font-size: 92px;
    letter-spacing: 0.14em;
    line-height: 1;
    padding-left: 0.14em;
  }
  .person-title {
    margin-top: 22px;
    font-weight: 500;
    font-size: 46px;
    line-height: 1.1;
  }
  .firm-mark {
    position: absolute;
    top: 470px;
    left: 0;
    right: 0;
    display: flex;
    justify-content: center;
    align-items: center;
    gap: 18px;
  }
  .firm-mark-dot {
    width: 22px;
    height: 22px;
    border-radius: 50%;
    background: var(--ink-navy);
  }
  .firm-name {
    font-weight: 600;
    font-size: 44px;
    letter-spacing: 0.04em;
    text-transform: uppercase;
  }
  .contact {
    position: absolute;
    top: 670px;
    left: 0;
    right: 0;
    font-weight: 500;
    font-size: 42px;
    line-height: 1.55;
  }
  .contact-divider { padding: 0 0.5em; }
</style>
</head>
<body>
  <main class="business-card">
    <section class="identity">
      <h1 class="person-name">JORDAN HALE</h1>
      <p class="person-title">Senior Wealth Advisor</p>
    </section>

    <div class="firm-mark">
      <span class="firm-mark-dot"></span>
      <span class="firm-name">Veroma Wealth</span>
    </div>

    <address class="contact" style="font-style: normal;">
      <div class="contact-line">jordan@veromawealth.com<span class="contact-divider">|</span>+1(555) 410-2387</div>
      <div class="contact-line">veromawealth.com</div>
    </address>
  </main>
</body>
</html>
```